Business Report Cover

We need a revamped quarterly report cover to send to our clients. We asset manage commercial and residential properties throughout the the United States. We use a .pdf version of a cover that we've used for years but would like a fresh updated look for 2018. The cover should include our company logo (KOV Enterprises) and a photo of the property as well as the Quarter/Year of the report.

```html
<!DOCTYPE html>
<html lang="en">
<head>
<meta charset="utf-8">
<title>KOV Enterprises — Quarterly Operating Report, 1st Quarter 2018</title>
<link rel="stylesheet" href="https://fonts.googleapis.com/css2?family=Didact+Gothic&display=swap">
<style>
  :root {
    --canvas-bg: #ecebe8;
    --paper: #ffffff;
    --ink: #141414;
    --photo-sky: #d4d3d5;
    --photo-horizon: #b9b5b8;
    --photo-mid: #7d7177;
    --photo-ground: #574c52;
    --photo-deep: #4a4045;
    --year-text: #ffffff;
  }

  * { margin: 0; padding: 0; box-sizing: border-box; }

  html, body {
    width: 1200px;
    height: 1200px;
    overflow: hidden;
    background: var(--canvas-bg);
  }

  .cover {
    position: absolute;
    left: 187px;
    top: 20px;
    width: 990px;
    height: 1390px;
    transform: scale(0.832);
    transform-origin: top left;
    background: var(--paper);
    font-family: "Didact Gothic", "Helvetica Neue", Arial, sans-serif;
    color: var(--ink);
  }

  .brand {
    position: absolute;
    top: 62px;
    left: 0;
    width: 100%;
    text-align: center;
    color: var(--ink);
    text-transform: uppercase;
    line-height: 1;
  }

  .brand-mark {
    display: block;
    font-size: 64px;
    letter-spacing: 0.02em;
  }

  .brand-sub {
    display: block;
    margin-top: 8px;
    font-size: 17px;
    letter-spacing: 0.42em;
    padding-left: 0.42em;
  }

  .property-photo {
    position: absolute;
    left: 37px;
    top: 205px;
    width: 920px;
    height: 905px;
    background: linear-gradient(
      to bottom,
      var(--photo-sky) 0%,
      var(--photo-sky) 30%,
      var(--photo-horizon) 40%,
      var(--photo-mid) 50%,
      var(--photo-ground) 60%,
      var(--photo-deep) 100%
    );
  }

  .report-year {
    position: absolute;
    right: 52px;
    top: 1000px;
    font-size: 92px;
    line-height: 1;
    letter-spacing: -0.03em;
    color: var(--year-text);
  }

  .report-title {
    position: absolute;
    right: 48px;
    top: 1140px;
    text-align: right;
    font-weight: 400;
    font-size: 32px;
    line-height: 1.28;
    letter-spacing: -0.02em;
    word-spacing: -0.05em;
    text-transform: uppercase;
  }

  .property-address {
    position: absolute;
    left: 0;
    width: 100%;
    top: 1350px;
    text-align: center;
    font-size: 19px;
  }
</style>
</head>
<body>
  <main class="cover">
    <header class="brand" aria-label="KOV Enterprises">
      <span class="brand-mark">KOV</span>
      <span class="brand-sub">Enterprises</span>
    </header>

    <div class="property-photo" role="img" aria-label="Halftone photograph of the property: a corner convenience store with fuel canopy and pumps under an overcast sky"></div>

    <div class="report-year">2018</div>

    <h1 class="report-title">
      <span>Quarterly Operating Report</span><br>
      <span>1st Quarter</span>
    </h1>

    <p class="property-address">Lakemont Corner Market 4120 NE Birchwood Ave. Lakemont, WA 98000</p>
  </main>
</body>
</html>
```